Sable Grove products by Voldrin. Beauty, skin care cosmetic products

We are an all natural and organic beauty product company looking for a logo an label design ideas. Our motto is to make products that are safe, natural, in harmony with the earth and that really work. Our products will contribute to the transition from the Old Earth to the Sable Grove (as the image of the two worlds suggests). The earths can be mixed in the label. The label example is a rough sketch.
Updates

The label needs to be 1 (one) inch high and 7 inch long.

Need extra days to review

Target Market(s)

Products made with natural and organic ingredients. Beauty and skin products

Requirements
Must have
• My project must be standing out. We want customers to be draw to he product on the shelf. Wow, this label is different? what is it? All natural? I must try it.
• Must be bold but not outrageous.
• The two earth can be placed on right and left side of the tree of life on the second attachment
Nice to have
• The two Earth can be in the back ground suggesting that this product takes us from chemically and artificially filled products to something new that is in harmony with nature and health.
Should not have
• Should not be boring. Ordinary, easy to forget and ignore patterns, lettering, logos.

```html
<!DOCTYPE html>
<html lang="en">
<head>
<meta charset="utf-8">
<title>Sable Grove Under-Arm-Balm Label</title>
<link rel="stylesheet" href="https://fonts.googleapis.com/css2?family=Marcellus&family=Ubuntu:wght@400;700&family=Open+Sans:wght@400;700&display=swap">
<style>
  :root {
    --page: #e4e4e6;
    --label-blue: #1f5fb8;
    --label-deep: #0b2a5c;
    --label-night: #07101e;
    --leaf-green: #7ccf3a;
    --ink-white: #ffffff;
    --box-black: #000000;
    --badge-red: #c9232e;
  }
  * { box-sizing: border-box; margin: 0; padding: 0; }
  html, body { width: 1200px; height: 985px; overflow: hidden; background: var(--page); }
  .label {
    position: absolute; left: 40px; top: 412px; width: 1120px; height: 160px;
    overflow: hidden; color: var(--ink-white);
    box-shadow: 0 10px 22px rgba(0,0,0,.25);
  }
  .label-art {
    position: absolute; inset: 0;
    background:
      radial-gradient(ellipse 220px 200px at 560px 80px, #0a1a24 0%, #0c2a3a 55%, rgba(16,60,110,0) 100%),
      radial-gradient(ellipse 260px 200px at 330px 40px, rgba(10,30,60,.6), rgba(10,30,60,0)),
      radial-gradient(ellipse 200px 160px at 880px 110px, rgba(20,40,90,.7), rgba(20,40,90,0)),
      linear-gradient(90deg, var(--label-blue) 0%, var(--label-deep) 35%, var(--label-night) 50%, var(--label-deep) 65%, var(--label-blue) 100%);
  }
  .ingredients {
    position: absolute; left: 24px; top: 19px; width: 300px;
    font-family: "Marcellus", serif; font-size: 9px; line-height: 12px;
  }
  .ingredients p { margin-bottom: 5px; }
  .ingredients b { font-family: "Ubuntu", sans-serif; font-weight: 700; }
  .warning {
    position: absolute; left: 17px; top: 114px; width: 303px; height: 35px;
    border: 1px solid var(--ink-white); padding: 4px 7px;
    font-family: "Marcellus", serif; font-size: 9px; line-height: 12px;
  }
  .warning b { font-family: "Ubuntu", sans-serif; font-weight: 700; }
  .scent {
    position: absolute; left: 362px; top: 79px; transform: translate(-50%,-50%) rotate(-90deg);
    font-family: "Marcellus", serif; font-size: 16px; color: var(--leaf-green); white-space: nowrap;
  }
  .center-line {
    position: absolute; left: 400px; width: 320px; text-align: center; white-space: nowrap;
  }
  .brand-name { top: 17px; font-family: "Marcellus", serif; font-size: 20px; line-height: 22px; }
  .brand-by { top: 38px; font-family: "Marcellus", serif; font-size: 12px; line-height: 22px; }
  .brand-by b { font-family: "Ubuntu", sans-serif; font-size: 19px; font-weight: 700; }
  .product-name {
    top: 72px; font-family: "Ubuntu", sans-serif; font-weight: 700; font-size: 22px; line-height: 28px;
    color: var(--leaf-green); letter-spacing: .5px;
  }
  .claims { top: 111px; font-family: "Marcellus", serif; font-size: 11px; line-height: 15px; }
  .free-from { top: 128px; font-family: "Open Sans", sans-serif; font-size: 10px; line-height: 15px; }
  .free-from b { font-weight: 700; }
  .maker {
    position: absolute; left: 799px; top: 25px;
    font-family: "Marcellus", serif; font-size: 10px; line-height: 13px;
  }
  .site { position: absolute; left: 799px; top: 64px; font-family: "Marcellus", serif; font-size: 10px; }
  .site span { font-size: 14px; }
  .best-before {
    position: absolute; left: 799px; top: 94px; width: 127px; height: 16px;
    background: var(--ink-white); color: #111; font-family: "Marcellus", serif; font-size: 9px;
    padding: 2px 7px;
  }
  .net-wt { position: absolute; left: 801px; top: 120px; font-family: "Marcellus", serif; font-size: 10px; }
  .badge { position: absolute; border-radius: 50%; }
  .badge-recycle { left: 992px; top: 16px; width: 34px; height: 34px; background: var(--leaf-green); }
  .badge-cruelty { left: 992px; top: 65px; width: 34px; height: 34px; background: var(--ink-white); }
  .badge-origin { left: 946px; top: 109px; width: 37px; height: 37px; background: var(--badge-red); border: 2px solid var(--ink-white); }
  .social {
    position: absolute; left: 988px; top: 122px; display: flex; align-items: center; gap: 3px;
    font-family: "Marcellus", serif; font-size: 7.5px;
  }
  .social i { width: 7px; height: 7px; border-radius: 50%; background: var(--ink-white); display: block; }
  .code-box { position: absolute; left: 1039px; top: 10px; width: 67px; height: 139px; background: var(--box-black); }
</style>
</head>
<body>
  <section class="label">
    <div class="label-art" role="img" aria-label="Illustration of two earths flanking a tree of life with knotwork ring, in deep blues and greens"></div>

    <div class="ingredients">
      <p><b>INGREDIENTS:</b> Organic Coconut (Cocos nucifera) Oil, Organic Bees Wax, Shea (Butyrospermum Parkii) Butter, Arrowroot (Manihot Esculenta) Powder, Magnesium Oil, Nahcolite (Natural Baking Soda)</p>
      <p><b>DIRECTIONS:</b> With the finger or spatula apply a pea size product under the arm and spread it on, if applied night after a shave it might sting a bit. Wait a few minutes and then apply.</p>
    </div>
    <div class="warning"><b>WARNING:</b> External use only. Discontinue use if irritation occurs. Do not apply to open cuts or wounds.</div>

    <div class="scent">Original Scent</div>

    <div class="center-line brand-name">Sable Grove Products</div>
    <div class="center-line brand-by">by <b>VOLDRIN</b></div>
    <div class="center-line product-name">UNDER-ARM-BALM</div>
    <div class="center-line claims">100% NATURAL INGREDIENTS</div>
    <div class="center-line free-from"><b>No</b> Aluminum, <b>No</b> Parabens, <b>No</b> Phthalates</div>

    <div class="maker">Manufactured by Voldrin LLC<br>Fenwick Hollow MD 20417</div>
    <div class="site">Lear more at: <span>VOLDRIN.COM</span></div>
    <div class="best-before">Best before: 11-21-11</div>
    <div class="net-wt">Net Wt. 2oz (56 g)</div>

    <div class="badge badge-recycle"></div>
    <div class="badge badge-cruelty"></div>
    <div class="badge badge-origin"></div>
    <div class="social"><i></i>@voldrin</div>

    <div class="code-box"></div>
  </section>
</body>
</html>
```